Business cards to launch an education platform

Hi,
I am looking at having new business cards designed.
I am a startup, developing a web platform for schools and university, the education world. It's an online assessment system.
I would like a card that looks classy, and that is using the colors and the font of my logo.

I have attached:
1) my logo
2) A business card that I have designed quickly so you can have all the information required in the card, but I really don't like it.
3) The font that I am using (Lato Regular) to design my web platform
4) Some screenshots of my web platform so you can have a look at the style that I have.

Target Market(s)

Major market: Education system: Schools and university
Minor markets: Business in general

Industry/Entity Type

Business

Contact Information for Business Card

Clara Fenwick
Director

M: 0437 518 902
E: clara.fenwick@amberLoomSystems.com.au

Requirements
Must have
• The colors of my logo

```html
<!DOCTYPE html>
<html lang="en">
<head>
<meta charset="utf-8">
<title>Amber Loom Systems — Business Cards</title>
<link rel="stylesheet" href="https://fonts.googleapis.com/css2?family=Lato:wght@400;700&family=Roboto+Condensed:wght@400;700&display=swap">
<style>
  :root {
    --backdrop: #e4e5e7;
    --paper: #eeeff1;
    --navy: #0a3b6e;
    --navy-deep: #053463;
    --royal: #0f5aa6;
    --cyan: #2cc3e6;
    --ink-grey: #4a4d52;
    --white: #ffffff;
  }
  * { box-sizing: border-box; margin: 0; padding: 0; }
  html, body { width: 1105px; height: 1200px; overflow: hidden; }
  body { background: var(--backdrop); position: relative; }

  .card {
    position: absolute;
    left: 182px;
    width: 746px;
    height: 425px;
    overflow: hidden;
  }
  .card--front { top: 120px; background: var(--paper); }
  .card--back  { top: 637px; background: var(--navy-deep); }

  /* Front */
  .brand-name {
    position: absolute;
    left: 40px;
    top: 226px;
    width: 300px;
    text-align: center;
    font-family: "Lato", sans-serif;
    font-weight: 400;
    font-size: 29px;
    line-height: 1.15;
    letter-spacing: 2px;
    color: var(--navy);
  }
  .person {
    position: absolute;
    left: 342px;
    top: 110px;
    font-family: "Roboto Condensed", sans-serif;
  }
  .person__name {
    font-weight: 700;
    font-size: 33px;
    color: var(--navy);
    line-height: 1.1;
  }
  .person__role {
    font-weight: 700;
    font-size: 22px;
    color: var(--ink-grey);
    margin-top: 4px;
  }
  .contact-list {
    list-style: none;
    margin-top: 26px;
  }
  .contact-list li {
    display: flex;
    align-items: center;
    gap: 14px;
    font-size: 16.5px;
    color: var(--ink-grey);
    height: 29px;
  }
  .contact-list svg { width: 16px; height: 16px; flex: none; }
  .footer-band {
    position: absolute;
    left: 0;
    bottom: 0;
    width: 746px;
    height: 62px;
    background: linear-gradient(90deg, #0a4a8c 0%, var(--royal) 55%, #0a3f7a 100%);
  }

  /* Back */
  .mark-area {
    position: absolute;
    left: 400px;
    top: 40px;
    width: 310px;
    height: 310px;
    background: radial-gradient(circle at 70% 60%, #1f8fd0 0%, #0e5ea8 55%, #0a4a8c 100%);
  }
  .back-brand {
    position: absolute;
    left: 56px;
    top: 266px;
    font-family: "Lato", sans-serif;
    font-weight: 400;
    color: var(--white);
  }
  .back-brand__name {
    font-size: 40px;
    letter-spacing: 3px;
    line-height: 1.1;
  }
  .back-brand__web {
    font-size: 20px;
    margin-top: 8px;
  }
</style>
</head>
<body>

  <section class="card card--front">
    <div class="brand-name">AMBER LOOM<br>SYSTEMS</div>

    <div class="person">
      <h1 class="person__name">Clara Fenwick</h1>
      <p class="person__role">Director</p>
      <ul class="contact-list">
        <li>
          <svg viewBox="0 0 16 16" aria-hidden="true"><rect x="4" y="1" width="8" height="14" rx="1.5" fill="none" stroke="#0a3b6e" stroke-width="1.6"/><rect x="7" y="12" width="2" height="1.4" fill="#0a3b6e"/></svg>
          0437 518 902
        </li>
        <li>
          <svg viewBox="0 0 16 16" aria-hidden="true"><rect x="1" y="3.5" width="14" height="9" fill="#0a3b6e"/><path d="M1 4 L8 9 L15 4" fill="none" stroke="#eeeff1" stroke-width="1.2"/></svg>
          clara.fenwick@amberLoomSystems.com.au
        </li>
        <li>
          <svg viewBox="0 0 16 16" aria-hidden="true"><circle cx="8" cy="8" r="6.5" fill="#0a3b6e"/><path d="M1.5 8 H14.5 M8 1.5 C5 5 5 11 8 14.5 M8 1.5 C11 5 11 11 8 14.5" fill="none" stroke="#eeeff1" stroke-width="0.9"/></svg>
          www.amberLoomSystems.com.au
        </li>
      </ul>
    </div>

    <div class="footer-band" role="img" aria-label="Decorative blue wave band"></div>
  </section>

  <section class="card card--back">
    <div class="mark-area" role="img" aria-label="Brand mark area"></div>
    <div class="back-brand">
      <p class="back-brand__name">AMBER LOOM<br>SYSTEMS</p>
      <p class="back-brand__web">amberLoomSystems.com.au</p>
    </div>
  </section>

</body>
</html>
```